Book Cover on Entrepreneurship for Eye Doctors

Book Title: The Lens Practice Builder: How to launch with confidence
Author: Rufus Tembley, Optom, MBA, DBA, EIC
I need a Book Cover with the following descriptions:
Topic: the book topic is entrepreneurship knowledge for eye care professionals.
The book's audience: eye care professionals who you know as Opticians, who sell eyeglasses and sunglasses;
Optometrists, test eyes, fit contact lenses, and prescribe medication
Ophthalmologists, perform eye surgery
More about the audience:
1- Young eye care professionals who don’t know about entrepreneurship and those who are stuck in the 9-to-5 job;
2- This is the first book written on entrepreneurship with eye care professionals in mind.
3- Private practice owners the established business guys who are looking to grow their business;
4- Many eye care professionals are MBA holders they may have learned a little bit about entrepreneurship during their MBA studies.
Use the sample cover above and the suggestions that follow as a guide:
1- The cover should be very simple leaving an empty space somewhere to sign the book;
2- The Title and author name should use a modern font;
3- The cover should provide info about what's inside the book through illustrations, for example:
a- Gears: illustrating entrepreneur growth mindset (or anything more explicit)
b- Spectacles, sunglasses, lenses, eye drops, or any other eye care-related correction tools illustrating eye care (or anything more explicit)
c- Symbols illustrating ideas, opportunity, and profit, like money, charts, light bulbs, brain, and coins,...(or anything more explicit)
d- Entrepreneurship illustrated by Briefcase, tie, suit,... (or anything more explicit)

The rest is your creativity and imagination interplay.

Target Market(s)

Eye care professionals: Opticians, Optometrists, Ophthalmologists, Eye Care Administrators, Students in eye specialties.

Industry/Entity Type

eye care

Requirements
Must have
• 1- The cover should be very simple leaving an empty space somewhere to sign the book; 2- The Title and author name should use a modern font; 3- The cover should provide info about what's inside the book through illustrations, for example: a- Gears: illustrating entrepreneur growth mindset (or anything more explicit) b- Spectacles, sunglasses, lenses, eye drops, or any other eye care-related correction tools illustrating eye care (or anything more explicit) c- Symbols illustrating ideas, opportunity, and profit, like money, charts, light bulbs, brain, and coins,...(or anything more explicit) d- Entrepreneurship illustrated by Briefcase, tie, suit,... (or anything more explicit)

```html
<!DOCTYPE html>
<html lang="en">
<head>
<meta charset="UTF-8">
<title>The Lens Practice Builder – Book Cover</title>
<link href="https://fonts.googleapis.com/css2?family=Bebas+Neue&family=Oswald:wght@500;600&family=Libre+Baskerville:ital@1&family=Roboto+Condensed:wght@400&display=swap" rel="stylesheet">
<style>
  :root {
    --stage: #e9eaec;
    --paper: #ffffff;
    --navy: #163f6d;
    --cyan: #13a6cc;
    --sky: #cfe4f2;
    --body-light: #b8d3ea;
    --rule: #7cc6dd;
  }
  * { box-sizing: border-box; margin: 0; padding: 0; }
  html, body { width: 1200px; height: 1200px; overflow: hidden; }
  body { background: var(--stage); position: relative; font-family: "Roboto Condensed", sans-serif; }

  .cover { position: absolute; top: 170px; height: 860px; box-shadow: 0 10px 30px rgba(0,0,0,.12); }
  .front { left: 105px; width: 440px; background: var(--paper); }
  .back { left: 605px; width: 440px; background: var(--navy); }
  .spine { position: absolute; top: 170px; left: 1045px; width: 50px; height: 860px; background: var(--paper); box-shadow: 0 10px 30px rgba(0,0,0,.12); }

  .front-title { position: absolute; left: 0; top: 40px; width: 440px; height: 360px; }
  .title-text { font-family: "Bebas Neue", sans-serif; }
  .series-mark { position: absolute; right: 42px; top: 398px; font-family: "Oswald", sans-serif; font-weight: 600; font-size: 17px; color: var(--navy); letter-spacing: .5px; }
  .tagline { position: absolute; left: 48px; right: 48px; top: 440px; height: 72px; border-top: 1.5px solid var(--rule); border-bottom: 1.5px solid var(--rule); display: flex; align-items: center; justify-content: center; font-family: "Libre Baskerville", serif; font-style: italic; font-size: 17px; color: var(--navy); }
  .front-artwork { position: absolute; left: 55px; top: 540px; width: 330px; height: 210px; }
  .front-author { position: absolute; left: 0; right: 0; top: 785px; text-align: center; font-family: "Oswald", sans-serif; font-weight: 600; font-size: 19px; letter-spacing: 1.5px; color: var(--navy); }
  .front-author .credentials { color: var(--cyan); }

  .back-title { position: absolute; left: 90px; top: 38px; width: 260px; height: 230px; }
  .blurb { position: absolute; left: 30px; right: 30px; top: 282px; color: var(--body-light); font-size: 10.5px; line-height: 1.42; text-align: justify; }
  .back-author { position: absolute; left: 0; right: 0; top: 586px; text-align: center; font-family: "Oswald", sans-serif; font-weight: 500; font-size: 13.5px; letter-spacing: 1.4px; color: var(--paper); }
  .author-portrait { position: absolute; left: 30px; top: 620px; width: 110px; height: 195px; background: var(--paper); }
  .author-bio { position: absolute; left: 150px; right: 30px; top: 618px; color: var(--body-light); font-size: 10.2px; line-height: 1.42; text-align: justify; }

  .spine-label { position: absolute; inset: 0; }
</style>
</head>
<body>

  <section class="cover front">
    <svg class="front-title" viewBox="0 0 440 360" aria-label="The Lens Practice Builder">
      <text class="title-text" x="220" y="128" text-anchor="middle" font-size="148" fill="var(--navy)" textLength="344" lengthAdjust="spacingAndGlyphs">THE LENS</text>
      <text class="title-text" x="220" y="252" text-anchor="middle" font-size="140" fill="var(--navy)" textLength="344" lengthAdjust="spacingAndGlyphs">PRACTICE</text>
      <text class="title-text" x="220" y="346" text-anchor="middle" font-size="106" fill="var(--cyan)" textLength="344" lengthAdjust="spacingAndGlyphs">BUILDER</text>
    </svg>
    <div class="series-mark">BOOK - 2</div>
    <div class="tagline">How to launch with confidence</div>
    <svg class="front-artwork" viewBox="0 0 330 210" role="img" aria-label="Illustration of two profile heads, one growing a plant with gears and an eye, the other holding a caged figure, with a person carrying a coin bulb leaping between them over a briefcase">
      <path d="M40 30 C80 -5 150 10 190 20 C240 30 300 5 318 55 C335 100 300 120 305 160 C310 200 250 212 200 205 C150 198 100 212 60 195 C15 178 0 140 12 100 C22 68 10 55 40 30 Z" fill="var(--sky)"/>
    </svg>
    <div class="front-author">RUFUS TEMBLEY, <span class="credentials">OPTOM, MBA, DBA, EIC</span></div>
  </section>

  <section class="cover back">
    <svg class="back-title" viewBox="0 0 260 230" aria-label="The Lens Practice Builder">
      <text class="title-text" x="130" y="88" text-anchor="middle" font-size="100" fill="var(--paper)" textLength="218" lengthAdjust="spacingAndGlyphs">THE LENS</text>
      <text class="title-text" x="130" y="172" text-anchor="middle" font-size="96" fill="var(--paper)" textLength="218" lengthAdjust="spacingAndGlyphs">PRACTICE</text>
      <text class="title-text" x="130" y="226" text-anchor="middle" font-size="62" fill="var(--cyan)" textLength="218" lengthAdjust="spacingAndGlyphs">BUILDER</text>
    </svg>
    <div class="blurb">
      <p>Lorem ipsum dolor sit amet, consectetuer adipiscing elit, sed diam nonummy nibh euismod tincidunt ut laoreet dolore magna aliquam erat volutpat. Ut wisi enim ad minim veniam, quis nostrud exerci tation ullamcorper suscipit lobortis nisl ut aliquip ex ea commodo consequat. Duis autem vel eum iriure dolor in hendrerit in vulputate velit esse molestie consequat, vel illum dolore eu feugiat nulla facilisis at vero eros et accumsan et iusto odio dignissim qui blandit praesent luptatum zzril delenit augue duis dolore te feugait nulla facilisi.</p>
      <p>Lorem ipsum dolor sit amet, cons ectetuer adipiscing elit, sed diam nonummy nibh euismod tincidunt ut laoreet dolore magna aliquam erat volutpat. Ut wisi enim ad minim veniam, quis nostrud exerci tation ullamcorper suscipit lobortis nisl ut aliquip ex ea commodo consequat.</p>
      <p>Lorem ipsum dolor sit amet, consectetuer adipiscing elit, sed diam nonummy nibh euismod tincidunt ut laoreet dolore magna aliquam erat volutpat. Ut wisi enim ad minim veniam, quis nostrud exerci tation ullamcorper suscipit lobortis nisl ut aliquip ex ea commodo consequat. Duis autem vel eum iriure dolor in hendrerit in vulputate velit esse molestie consequat, vel illum dolore eu feugiat nulla facilisis at</p>
    </div>
    <div class="back-author">RUFUS TEMBLEY, OPTOM, MBA, DBA, EIC</div>
    <div class="author-portrait" role="img" aria-label="Space for the author portrait"></div>
    <div class="author-bio">
      Lorem ipsum dolor sit amet, consectetuer adipiscing elit, sed diam nonummy nibh euismod tincidunt ut laoreet dolore magna aliquam erat volutpat. Ut wisi enim ad minim veniam, quis nostrud exerci tation ullamcorper suscipit lobortis nisl ut aliquip ex ea commodo consequat. Duis autem vel eum iriure dolor in hendrerit in vulputate velit esse molestie consequat, vel illum dolore eu feugiat nulla facilisis at vero eros et accumsan et iusto odio dignissim qui blandit praesent luptatum zzril delenit augue duis dolore te feugait nulla facilisi. Lorem ipsum dolor sit amet, cons ectetuer adipiscing elit, sed diam nonummy nibh euismod tincidunt ut laoreet dolore magna aliquam erat volutpat. Ut wisi enim ad
    </div>
  </section>

  <aside class="spine">
    <svg class="spine-label" viewBox="0 0 50 860" aria-label="Spine: The Lens Practice Builder, Rufus Tembley, Optom, MBA, DBA, EIC">
      <g transform="translate(25 830) rotate(-90)">
        <text x="0" y="8" font-family="Oswald, sans-serif" font-weight="600" font-size="24" letter-spacing="1">
          <tspan fill="var(--navy)">THE LENS PRACTICE </tspan><tspan fill="var(--cyan)">BUILDER</tspan>
        </text>
      </g>
      <g transform="translate(25 490) rotate(-90)">
        <text x="0" y="5" font-family="Oswald, sans-serif" font-weight="600" font-size="14" letter-spacing="1.5">
          <tspan fill="var(--navy)">RUFUS TEMBLEY, </tspan><tspan fill="var(--cyan)">OPTOM, MBA, DBA, EIC</tspan>
        </text>
      </g>
    </svg>
  </aside>

</body>
</html>
```